Basic business card

use my newly created logo - and the phrases (Quality Assured Lines & Verified Unified Build Validation) - and my new email domain / ID - use at conferences / tradeshows

Industry/Entity Type

semiconductor

Contact Information for Business Card

Daniel K Forde, Owner, communicate via Logo - Lower COT - Cost of Test, Accelerated NPI - New Product Introduction, phone +1 555 613 0946, Chandler, Arizona, USA, daniel.forde@qal-vub.com

Font styles to use
Sans Serif

Requirements
Nice to have
• re-use my logo created via Pixel Harbor last August (#7315926)

```html
<!DOCTYPE html>
<html lang="en">
<head>
<meta charset="utf-8">
<title>QAL-VUB Business Card</title>
<link href="https://fonts.googleapis.com/css2?family=Montserrat:wght@400;500;700&family=Oswald:wght@600&display=swap" rel="stylesheet">
<style>
  :root {
    --backdrop: #e6e8eb;
    --navy-light: #2a3a4d;
    --navy-dark: #0f1620;
    --wordmark-steel: #8ea3bd;
    --wordmark-ink: #3b4a5e;
    --accent-cyan: #0cb0e0;
    --edge-blue: #2a9be0;
    --text-dark: #2b2b2b;
    --paper: #ffffff;
  }
  * { margin: 0; padding: 0; box-sizing: border-box; }
  html, body { width: 1200px; height: 1200px; overflow: hidden; }
  body {
    background: var(--backdrop);
    font-family: "Montserrat", Arial, sans-serif;
    position: relative;
  }
  .card {
    position: absolute;
    top: 215px;
    width: 440px;
    height: 770px;
    border-radius: 34px;
    overflow: hidden;
    border: 3px solid var(--edge-blue);
  }
  .card--front {
    left: 120px;
    background: radial-gradient(ellipse at 45% 35%, var(--navy-light) 0%, #1c2735 50%, var(--navy-dark) 100%);
  }
  .front-brand {
    position: absolute;
    left: 50%;
    top: 50%;
    transform: translate(-50%, -50%) rotate(-90deg);
    display: flex;
    align-items: center;
    gap: 22px;
    white-space: nowrap;
  }
  .front-brand__mark {
    width: 26px;
    height: 26px;
    background: var(--wordmark-steel);
  }
  .front-brand__name {
    font-weight: 500;
    font-size: 92px;
    letter-spacing: 2px;
    color: var(--wordmark-steel);
  }
  .card--back {
    left: 640px;
    background: var(--paper);
    border-color: var(--accent-cyan);
  }
  .back-brand {
    position: absolute;
    left: 42px;
    top: 150px;
    display: flex;
    align-items: center;
    gap: 16px;
  }
  .back-brand__mark {
    width: 22px;
    height: 22px;
    background: var(--wordmark-ink);
  }
  .back-brand__name {
    font-weight: 500;
    font-size: 62px;
    letter-spacing: 1px;
    color: var(--wordmark-ink);
  }
  .contact {
    position: absolute;
    left: 56px;
    top: 380px;
  }
  .contact__name {
    font-weight: 700;
    font-size: 44px;
    line-height: 1;
    color: var(--accent-cyan);
    letter-spacing: -1px;
  }
  .contact__role {
    font-weight: 400;
    font-size: 24px;
    color: var(--text-dark);
    margin-top: 6px;
    letter-spacing: 1px;
  }
  .contact__email {
    display: flex;
    align-items: center;
    gap: 12px;
    margin-top: 34px;
    font-size: 25px;
    color: var(--text-dark);
  }
  .contact__email svg { width: 34px; height: 24px; flex: none; }
  .tagline-band {
    position: absolute;
    left: 0;
    right: 0;
    bottom: 55px;
    height: 150px;
    background: var(--accent-cyan);
    display: flex;
    align-items: center;
    justify-content: center;
    text-align: center;
    font-family: "Oswald", "Arial Narrow", sans-serif;
    font-weight: 600;
    font-size: 27px;
    line-height: 1.15;
    color: var(--paper);
    text-transform: uppercase;
  }
</style>
</head>
<body>
  <section class="card card--front" aria-label="Card front">
    <div class="front-brand">
      <span class="front-brand__mark"></span>
      <span class="front-brand__name">QAL-VUB</span>
    </div>
  </section>

  <section class="card card--back" aria-label="Card back">
    <div class="back-brand">
      <span class="back-brand__mark"></span>
      <span class="back-brand__name">QAL-VUB</span>
    </div>
    <div class="contact">
      <p class="contact__name">FULL NAME</p>
      <p class="contact__role">POSITION</p>
      <p class="contact__email">
        <svg viewBox="0 0 34 24" aria-hidden="true">
          <rect x="0" y="0" width="34" height="24" rx="2" fill="#0cb0e0"/>
          <polyline points="1,2 17,14 33,2" fill="none" stroke="#ffffff" stroke-width="2.5"/>
        </svg>
        email@company.com
      </p>
    </div>
    <div class="tagline-band">
      <p>Quality Assured Lines &amp; Verified<br>Unified Build Validation</p>
    </div>
  </section>
</body>
</html>
```